Tech business card design

We need an amazing business card design for our new business 'Pexla' a marketing tech startup based in Sydney, Australia. We provide an online marketplace for businesses to search and buy advertising media, connect with service providers and learn more about marketing. We wish to communicate 'cool tech', reliability and professionalism and design based around our logo.

Target Market(s)

Business Owners

Contact Information for Business Card

Name
Position
Email Address
Website
Phone Number

Font styles to use
Other font styles liked:
• Avenir & Avenir Next

Colors

Designer to choose colors to be used in the design.

```html
<!DOCTYPE html>
<html lang="en">
<head>
<meta charset="utf-8">
<title>Pexla Business Card</title>
<link rel="stylesheet" href="https://fonts.googleapis.com/css2?family=Nunito+Sans:wght@400;800;900&display=swap">
<style>
  :root {
    --backdrop: #1f1f20;
    --navy: #141d4a;
    --navy-deep: #0f1740;
    --navy-pattern: #1a2556;
    --paper: #ffffff;
    --paper-tint: #f1f2f5;
    --ink-muted: #5a5f70;
  }
  * { box-sizing: border-box; margin: 0; padding: 0; }
  html, body {
    width: 1200px; height: 996px; overflow: hidden;
    background: var(--backdrop);
    font-family: "Nunito Sans", Arial, sans-serif;
  }
  .canvas { position: relative; width: 1200px; height: 996px; }

  .card {
    position: absolute;
    width: 525px; height: 300px;
    border-radius: 3px;
    overflow: hidden;
    box-shadow: 0 14px 30px rgba(0,0,0,.45);
  }

  /* Front */
  .card--front { left: 610px; top: 150px; background: var(--paper); }
  .front__texture {
    position: absolute; inset: 0;
    background: radial-gradient(ellipse at 60% 55%, var(--paper-tint) 0%, var(--paper) 75%);
  }
  .front__identity { position: absolute; left: 58px; top: 28px; }
  .front__name {
    font-weight: 900; font-size: 19px; letter-spacing: .5px;
    color: var(--navy);
  }
  .front__role { font-size: 12px; color: var(--ink-muted); margin-top: 1px; }

  .front__contact-tab {
    position: absolute; left: 0; top: 90px;
    width: 30px; height: 68px;
    background: var(--navy);
    border-radius: 0 12px 12px 0;
    display: flex; flex-direction: column; justify-content: space-evenly; align-items: center;
  }
  .front__contact-tab svg { width: 12px; height: 12px; }
  .front__contact-list {
    position: absolute; left: 40px; top: 92px;
    list-style: none;
    font-size: 13px; line-height: 21px; color: var(--ink-muted);
  }

  .front__wordmark {
    position: absolute; right: 44px; bottom: 30px;
    font-weight: 900; font-size: 100px; line-height: 1;
    letter-spacing: -2px;
    color: var(--navy);
  }
  .front__tm {
    position: absolute; right: 26px; bottom: 32px;
    font-size: 10px; font-weight: 800; color: var(--navy);
  }

  /* Back */
  .card--back { left: 70px; top: 520px; background: var(--navy-deep); }
  .back__pattern {
    position: absolute; inset: 0;
    background: linear-gradient(135deg, var(--navy-pattern) 0%, var(--navy-deep) 100%);
  }
  .back__wordmark {
    position: absolute; left: 0; right: 0; top: 50%;
    transform: translateY(-50%);
    text-align: center;
    font-weight: 900; font-size: 48px; letter-spacing: -1px;
    color: var(--paper);
  }
</style>
</head>
<body>
<main class="canvas">

  <section class="card card--front" aria-label="Business card front">
    <div class="front__texture" role="img" aria-label="Faint line-icon pattern of marketing and business symbols"></div>

    <header class="front__identity">
      <h1 class="front__name">JORDAN REYES</h1>
      <p class="front__role">Managing Director</p>
    </header>

    <div class="front__contact-tab" aria-hidden="true">
      <svg viewBox="0 0 12 12"><path d="M2.5 1h2l1 2.5-1.3 1a6 6 0 0 0 3.3 3.3l1-1.3L11 7.5v2a1.5 1.5 0 0 1-1.5 1.5A8.5 8.5 0 0 1 1 2.5 1.5 1.5 0 0 1 2.5 1z" fill="#fff"/></svg>
      <svg viewBox="0 0 12 12"><rect x="1" y="2.5" width="10" height="7" rx="1" fill="#fff"/><path d="M1.5 3l4.5 3.5L10.5 3" stroke="#141d4a" stroke-width="1" fill="none"/></svg>
      <svg viewBox="0 0 12 12" fill="none" stroke="#fff" stroke-width="1.1"><circle cx="6" cy="6" r="4.8"/><ellipse cx="6" cy="6" rx="2" ry="4.8"/><path d="M1.2 6h9.6"/></svg>
    </div>
    <ul class="front__contact-list">
      <li>020-555-0184</li>
      <li>info@pexlamail.com</li>
      <li>www.pexlamail.com</li>
    </ul>

    <p class="front__wordmark">pexla</p>
    <span class="front__tm">TM</span>
  </section>

  <section class="card card--back" aria-label="Business card back">
    <div class="back__pattern" role="img" aria-label="Tone-on-tone repeating brand name pattern in navy"></div>
    <p class="back__wordmark">pexla</p>
  </section>

</main>
</body>
</html>
```